Harbor Ledger Funds Bus card and Logo

I need a logo design and Bus card design. The fund focuses on evaluating and investing in minerals (sub-surface rights) and real estate.

Harbor ledger refers to a book of knowledge that each plebe gets when entering the Kelmont Marine Academy (my alma mater)

Target Market(s)

Investors and financial advisors

Contact Information for Business Card

Simple - perhaps a logo with a theme on book of knowledge

Logo Text

Ex Scientia Imperium

Font styles to use
Serif
Sans Serif

Colors

Designer to choose colors to be used in the design.

Requirements
Must have
• memorable logo that is relatively simple

```html
<!DOCTYPE html>
<html lang="en">
<head>
<meta charset="utf-8">
<title>Harbor Ledger Funds – Business Card</title>
<link href="https://fonts.googleapis.com/css2?family=Montserrat:wght@600&family=Roboto:wght@500&family=Work+Sans:wght@400&display=swap" rel="stylesheet">
<style>
  :root {
    --navy: #163a66;
    --sky: #0aa6e6;
    --ink: #1c3557;
    --paper: #ffffff;
    --backdrop: #262626;
  }
  * { margin: 0; padding: 0; box-sizing: border-box; }
  html, body { width: 1200px; height: 900px; overflow: hidden; }
  body { background: var(--backdrop); position: relative; font-family: "Work Sans", Arial, sans-serif; }

  .card {
    position: absolute; left: 261px; width: 656px; height: 357px;
    box-shadow: 0 6px 14px rgba(0,0,0,.5); overflow: hidden;
  }
  .card--front { top: 69px; background: var(--paper); }
  .card--back { top: 472px; background: var(--navy); }

  .brand {
    position: absolute; display: flex; flex-direction: column; align-items: center;
    font-family: "Montserrat", Arial, sans-serif; font-weight: 600; line-height: 1;
    white-space: nowrap;
  }
  .brand__dot { border-radius: 50%; background: var(--sky); }
  .brand__name { letter-spacing: 1px; }
  .brand__sub { letter-spacing: 1px; }

  .card--front .brand { left: 31px; top: 28px; color: var(--navy); }
  .card--front .brand__dot { width: 50px; height: 50px; margin-bottom: 19px; }
  .card--front .brand__name { font-size: 30px; }
  .card--front .brand__sub { font-size: 17px; margin-top: 8px; }

  .person { position: absolute; right: 31px; top: 169px; text-align: right; }
  .person__name { font-family: "Roboto", Arial, sans-serif; font-weight: 500; font-size: 28px; color: var(--sky); line-height: 1; }
  .person__role { font-size: 16px; color: var(--ink); margin-top: 4px; letter-spacing: .5px; }

  .rule { position: absolute; left: 31px; right: 31px; top: 229px; height: 1.5px; background: var(--navy); }

  .contacts { position: absolute; left: 31px; top: 253px; list-style: none; }
  .contacts li { display: flex; align-items: center; font-size: 15.5px; color: var(--ink); height: 21px; letter-spacing: .4px; }
  .contacts svg { width: 11px; height: 11px; margin-right: 8px; }
  .contacts .accent { color: var(--sky); }

  .address { position: absolute; right: 31px; top: 274px; text-align: right; font-size: 15.5px; color: var(--ink); line-height: 21px; letter-spacing: .4px; font-style: normal; }

  .footer-band { position: absolute; left: 0; bottom: 0; width: 656px; height: 30px; }

  .card--back .brand { left: 0; right: 0; top: 100px; color: var(--paper); }
  .card--back .brand__dot { width: 70px; height: 70px; margin-bottom: 24px; }
  .card--back .brand__name { font-size: 42px; }
  .card--back .brand__sub { font-size: 27px; margin-top: 6px; }
</style>
</head>
<body>

<section class="card card--front">
  <div class="brand">
    <span class="brand__dot"></span>
    <span class="brand__name">HARBOR LEDGER</span>
    <span class="brand__sub">FUNDS LLC</span>
  </div>

  <div class="person">
    <p class="person__name">DANIEL CARVER</p>
    <p class="person__role">Director</p>
  </div>

  <div class="rule"></div>

  <ul class="contacts">
    <li>
      <svg viewBox="0 0 12 12" aria-hidden="true"><path d="M2.5 1 L4.5 1 L5 3.5 L3.8 4.5 Q5 7.2 7.5 8.2 L8.5 7 L11 7.5 L11 9.5 Q10.5 11 9 11 Q1 10 1 3 Q1 1.5 2.5 1 Z" fill="var(--sky)"/></svg>
      +1 555 318-0246
    </li>
    <li>
      <svg viewBox="0 0 12 12" aria-hidden="true"><rect x="1" y="2.5" width="10" height="7" fill="none" stroke="var(--sky)" stroke-width="1.2"/><path d="M1 2.5 L6 6.5 L11 2.5" fill="none" stroke="var(--sky)" stroke-width="1.2"/></svg>
      info@harborledgerfunds.com
    </li>
    <li>
      <svg viewBox="0 0 12 12" aria-hidden="true"><g fill="none" stroke="var(--sky)" stroke-width="1"><circle cx="6" cy="6" r="5"/><ellipse cx="6" cy="6" rx="2.2" ry="5"/><path d="M1 6 H11 M2 3.5 H10 M2 8.5 H10"/></g></svg>
      www.<span class="accent">harborledgerfunds</span>.com
    </li>
  </ul>

  <address class="address">
    1187 Larkspur Lane<br>
    Cedar Glen, CA 95412
  </address>

  <svg class="footer-band" viewBox="0 0 656 30" preserveAspectRatio="none" aria-hidden="true">
    <path d="M0 19 L380 19 Q400 19 420 10 Q440 1 462 1 L656 1 L656 30 L0 30 Z" fill="var(--navy)"/>
    <path d="M0 18 L375 18 Q395 18 412 11 Q420 8 430 8 L380 8 Q372 8 360 8 L0 8 Z" fill="var(--paper)"/>
    <path d="M0 8 L380 8 Q392 8 400 12 Q390 14 378 14 L0 14 Z" fill="var(--sky)"/>
  </svg>
</section>

<section class="card card--back">
  <div class="brand">
    <span class="brand__dot"></span>
    <span class="brand__name">HARBOR LEDGER</span>
    <span class="brand__sub">FUNDS LLC</span>
  </div>
</section>

</body>
</html>
```